Beacon Advisory Website

I currently have a website www.beaconadvisoryinc.com. We are a IT Consulting Company. Our website will pretty much tell out our services. I am looking to enhance my website and make it look more professional. Looking for very classy and Contemporary look and design for my website.

It Company

```html
<!DOCTYPE html>
<html lang="en">
<head>
<meta charset="utf-8">
<title>Beacon Advisory — IT Consulting</title>
<link href="https://fonts.googleapis.com/css2?family=Oswald:wght@400;500&family=Source+Sans+3:wght@400;600&display=swap" rel="stylesheet">
<style>
:root{
  --white:#ffffff;
  --ink:#333333;
  --muted:#666666;
  --light-bg:#f5f5f5;
  --footer-bg:#f1f1f1;
  --brand-dark:#17457f;
  --brand-blue:#1a9ad6;
  --title-blue:#1b5ea3;
  --band-navy:#1760a6;
  --band-sky:#0699d8;
  --rule:#1b74bd;
  --dot-off:#c9c9c9;
}
*{box-sizing:border-box;margin:0;padding:0}
html,body{width:1200px;height:2647px;overflow:hidden}
body{position:relative;background:var(--white);font-family:"Source Sans 3",Arial,sans-serif;color:var(--ink)}

/* header */
.site-header{position:absolute;left:0;top:0;width:1200px;height:106px;background:var(--white)}
.brand{position:absolute;display:flex;align-items:center;gap:10px;font-weight:600;font-size:24px;color:var(--brand-dark);letter-spacing:.5px;text-transform:uppercase}
.brand-mark{width:34px;height:34px;background:var(--brand-blue)}
.site-header .brand{left:115px;top:36px}
.main-nav{position:absolute;top:63px;left:0;width:1200px;font-size:13.5px;font-weight:600;color:var(--ink);letter-spacing:.3px}
.main-nav span{position:absolute;white-space:nowrap}

/* hero */
.hero{position:absolute;left:0;top:106px;width:1200px;height:499px;overflow:hidden}
.hero-photo{position:absolute;inset:0;
  background:radial-gradient(ellipse at 40% 45%,#d3e3f1 0%,#9dbedc 35%,#5c8bbd 70%,#2f5d92 100%)}
.hero-word{position:absolute;font-family:"Oswald","Arial Narrow",sans-serif;color:var(--white);text-transform:uppercase;font-weight:500;text-shadow:0 1px 3px rgba(0,0,0,.25);white-space:nowrap}
.hero-word.small{font-size:28px;top:218px}
.hero-word.large{font-size:56px;top:198px;left:356px}
.slider-dots{position:absolute;display:flex;gap:7px}
.slider-dots i{display:block;width:9px;height:9px;border-radius:50%;background:var(--white)}
.slider-dots i.on{background:var(--brand-blue)}

/* welcome */
.welcome{position:absolute;left:0;top:605px;width:1200px;height:339px;background:var(--light-bg);text-align:center}
.section-title{font-size:22px;font-weight:600;text-transform:uppercase;letter-spacing:.3px}
.welcome .section-title{position:absolute;top:58px;width:100%;color:var(--brand-blue)}
.welcome p{position:absolute;left:180px;top:132px;width:840px;font-size:13px;line-height:24px;color:var(--muted)}
.btn-more{position:absolute;left:545px;top:266px;width:111px;height:36px;border:1px solid #8a8a8a;font-size:12px;font-weight:600;color:var(--title-blue);line-height:34px;letter-spacing:.3px}

/* services */
.services{position:absolute;left:0;top:944px;width:1200px;height:441px;background:var(--white)}
.services .section-title{position:absolute;top:64px;width:100%;text-align:center;color:var(--title-blue)}
.service{position:absolute;top:174px;width:288px}
.service-head{display:flex;align-items:center;gap:10px;height:60px;border-bottom:3px solid var(--rule)}
.service-icon{width:60px;height:60px;border-radius:50%;background:var(--brand-blue);display:flex;align-items:center;justify-content:center;position:relative;top:-8px}
.service-name{font-size:18px;color:#444;text-transform:uppercase;position:relative;top:-8px}
.service p{margin-top:20px;font-size:11px;line-height:19.5px;color:#555}
.services .slider-dots{left:566px;top:400px}
.services .slider-dots i{background:var(--dot-off)}
.services .slider-dots i.on{background:var(--brand-blue)}

/* feature bands */
.feature{position:absolute;left:0;width:1200px;height:355px}
.feature.navy{background:var(--band-navy);color:var(--white)}
.feature.plain{background:var(--white)}
.feature.sky{background:var(--band-sky);color:var(--white)}
.feature-photo{position:absolute;width:310px;height:310px;border-radius:50%;border:5px solid var(--white);box-shadow:0 2px 8px rgba(0,0,0,.25)}
.feature-title{position:absolute;font-size:22px;font-weight:600;text-transform:uppercase;letter-spacing:.3px}
.feature-text{position:absolute;font-size:13px;line-height:24px}
.feature.plain .feature-title{color:var(--title-blue)}
.feature.plain .feature-text{color:var(--muted)}

/* footer */
.site-footer{position:absolute;left:0;top:2448px;width:1200px;height:199px;background:var(--footer-bg);text-align:center}
.site-footer .brand{left:50%;transform:translateX(-50%);top:36px}
.footer-nav{position:absolute;top:102px;width:100%;font-size:13px;font-weight:600;color:var(--ink);letter-spacing:.3px}
.footer-nav .sep{margin:0 24px;color:#555;font-weight:400}
.copyright{position:absolute;top:140px;width:100%;font-size:13px;font-weight:600;color:var(--ink)}
</style>
</head>
<body>

<header class="site-header">
  <div class="brand"><span class="brand-mark"></span>Beacon Advisory</div>
  <nav class="main-nav">
    <span style="left:415px">COMPANY</span>
    <span style="left:522px">SERVICES</span>
    <span style="left:626px">SOLUTIONS</span>
    <span style="left:743px">RESOURCES</span>
    <span style="left:863px">CAREER</span>
    <span style="left:956px">CONTACT US</span>
  </nav>
</header>

<section class="hero">
  <div class="hero-photo" role="img" aria-label="Business professional in a shirt and tie touching a glowing virtual interface, soft blue tones"></div>
  <div class="hero-word small" style="left:100px">Management</div>
  <div class="hero-word large">Consulting</div>
  <div class="hero-word small" style="left:723px">Development</div>
  <div class="hero-word small" style="left:1055px">Strategy</div>
  <div class="slider-dots" style="left:570px;top:460px"><i class="on"></i><i></i><i></i><i></i></div>
</section>

<section class="welcome">
  <h2 class="section-title">Welcome to Beacon Advisory</h2>
  <p>Today's IT market is a dynamic, fast-paced industry, with ever-increasing demands. Meeting these demands for over 25 years, Beacon Advisory maintains a global presence, aggressively recruiting expertly qualified IT and Management Professionals from around the world and cultivating key partnerships with corporations to understand their business models end-to-end, with a goal of delivering exceptional client service and ensuring a consistent delivery of the talent needed to drive results</p>
  <div class="btn-more">LEARN MORE</div>
</section>

<section class="services">
  <h2 class="section-title">Our Services</h2>

  <div class="service" style="left:145px">
    <div class="service-head">
      <div class="service-icon"><svg width="28" height="24" viewBox="0 0 28 24" aria-hidden="true"><g fill="#fff"><rect x="2" y="16" width="4" height="6"/><rect x="9" y="12" width="4" height="10"/><rect x="16" y="7" width="4" height="15"/><rect x="23" y="2" width="4" height="20"/></g></svg></div>
      <div class="service-name">Business</div>
    </div>
    <p>Lorem Ipsum is simply dummy text of the printing and typesetting industry. Lorem Ipsum has been the industry's standard dummy text ever since the 1500s, when an unknown printer took a galley of type and scrambled it to make a type specimen book.</p>
  </div>

  <div class="service" style="left:454px">
    <div class="service-head">
      <div class="service-icon"><svg width="24" height="28" viewBox="0 0 24 28" aria-hidden="true"><path d="M12 2a8 8 0 0 0-5 14.2V20h10v-3.8A8 8 0 0 0 12 2z" fill="none" stroke="#fff" stroke-width="2.4"/><rect x="8" y="22" width="8" height="2.5" fill="#fff"/></svg></div>
      <div class="service-name">Technology</div>
    </div>
    <p>Lorem Ipsum is simply dummy text of the printing and typesetting industry. Lorem Ipsum has been the industry's standard dummy text ever since the 1500s, when an unknown printer took a galley of type and scrambled it to make a type specimen book.</p>
  </div>

  <div class="service" style="left:768px">
    <div class="service-head">
      <div class="service-icon"><svg width="26" height="26" viewBox="0 0 26 26" aria-hidden="true"><rect x="3" y="5" width="17" height="17" rx="2" fill="none" stroke="#fff" stroke-width="2.2"/><path d="M10 16l1-4 10-10 3 3-10 10z" fill="#fff"/></svg></div>
      <div class="service-name">Application</div>
    </div>
    <p>Lorem Ipsum is simply dummy text of the printing and typesetting industry. Lorem Ipsum has been the industry's standard dummy text ever since the 1500s, when an unknown printer took a galley of type and scrambled it to make a type specimen book.</p>
  </div>

  <div class="slider-dots"><i class="on"></i><i></i><i></i><i></i></div>
</section>

<section class="feature navy" style="top:1385px">
  <div class="feature-photo" role="img" aria-label="Team working together at laptops in a bright modern office" style="left:142px;top:22px;background:linear-gradient(160deg,#dfe6ea 0%,#a9b8c2 45%,#6f7f75 80%,#3f8a3a 100%)"></div>
  <h3 class="feature-title" style="left:535px;top:46px">IT Consulting</h3>
  <div class="feature-text" style="left:535px;top:118px;width:510px">
    <p>Information technology should improve business results. Beacon Advisory helps companies make sure it does. We look at IT issues strategically, in the broader context of our clients' business. Our experts provide an objective, independent perspective to help companies realize the full potential of their IT resources, investments and assets.</p>
    <p style="margin-top:24px">We draw on global experience across industries and technologies to help solve companies' most complex IT challenges. More than 40% of our work is done in the context of major transformation in the business or in IT.</p>
  </div>
</section>

<section class="feature plain" style="top:1740px">
  <h3 class="feature-title" style="left:143px;top:68px">Staff Augmentation</h3>
  <p class="feature-text" style="left:143px;top:132px;width:510px">For years Beacon Advisory has been offering our customers the ability to augment their existing staff with temporary highly skilled IT professionals who can help address immediate short term needs. We know that often our customers have brief spikes in their need for reporting, for example. With internal IT teams focused on more strategic projects, it can be difficult to justify diverting a team member for a few weeks to relieve this short term pressure from business users. This is an ideal situation in which to consider bringing in one of our team.</p>
  <div class="feature-photo" role="img" aria-label="Silhouettes of business people standing before a glass office tower" style="left:749px;top:22px;background:linear-gradient(170deg,#eef3f9 0%,#b7cde6 40%,#5c82b5 75%,#1f3c66 100%)"></div>
</section>

<section class="feature sky" style="top:2093px">
  <div class="feature-photo" role="img" aria-label="Businessman in a white shirt reviewing documents at a desk" style="left:142px;top:20px;background:linear-gradient(150deg,#f3f1ee 0%,#d8d2ca 45%,#a59b90 80%,#6d665e 100%)"></div>
  <h3 class="feature-title" style="left:535px;top:95px">Offshore</h3>
  <p class="feature-text" style="left:535px;top:160px;width:510px">Our Offshore development model has a unique distinction of providing efficient software solutions with cost and quality advantage, using state-of-the-art technologies, having the capacity to handle large projects and, above all, the ability to execute timely deliveries.</p>
</section>

<footer class="site-footer">
  <div class="brand"><span class="brand-mark"></span>Beacon Advisory</div>
  <nav class="footer-nav">COMPANY<span class="sep">|</span>SERVICES<span class="sep">|</span>SOLUTIONS<span class="sep">|</span>RESOURCES<span class="sep">|</span>CAREER<span class="sep">|</span>CONTACT US</nav>
  <div class="copyright">© 2016 COMPANY NAME | ALL RIGHTS RESERVED</div>
</footer>

</body>
</html>
```